Business card for Luxury Portable Restroom Trailer company

We are a Luxury Portable Restroom Trailer Company Called FALCRIDGE HIRES. Based in Orange County California. We provide portable restroom trailers for events, such as, Weddings, Concerts, Charity events, Sporting events, Tournaments, Corporate events, ect. We rent and Sell the Luxury restrooms. Our colors are white, grey, and Orange. As you will see in the logo we uploaded.
There are 2 people in the company so the names and titles will change for the 3 people but card will remain the same. Here is the information for each Person: Dwight Penner CFO 555 318-0476
next Person: Leon Marchetti VP 555 318-0476
Next Person: Owen Marchetti CEO 555 318-0476
Information to include on the card: Luxury Restroom Trailers Rental and Sales. Weddings, Concerts, Charity, Sporting and Corp. Events.

```html
<!DOCTYPE html>
<html lang="en">
<head>
<meta charset="UTF-8">
<title>Falcridge Hires – Business Card</title>
<link href="https://fonts.googleapis.com/css2?family=Quicksand:wght@400;500;700&display=swap" rel="stylesheet">
<style>
  :root {
    --page-bg: #e6e3df;
    --card-bg: #1f1e1f;
    --orange: #e8672a;
    --white: #f2f2f2;
    --grey: #bdbdbd;
  }
  * { margin: 0; padding: 0; box-sizing: border-box; }
  html, body {
    width: 1200px;
    height: 900px;
    overflow: hidden;
    background: var(--page-bg);
    font-family: "Quicksand", sans-serif;
  }
  .sheet {
    width: 1200px;
    height: 900px;
    display: flex;
    flex-direction: column;
    align-items: center;
    justify-content: center;
    gap: 50px;
  }
  .card {
    width: 630px;
    height: 360px;
    background: var(--card-bg);
    box-shadow: 0 8px 24px rgba(0,0,0,0.25);
    display: flex;
    flex-direction: column;
    align-items: center;
    padding-top: 92px;
    color: var(--white);
    text-align: center;
  }
  .brand {
    display: flex;
    align-items: center;
    gap: 14px;
  }
  .brand-mark {
    width: 22px;
    height: 22px;
    background: var(--orange);
  }
  .brand-name {
    font-weight: 700;
    font-size: 44px;
    letter-spacing: 2px;
    color: var(--white);
    line-height: 1;
  }
  .divider {
    width: 360px;
    height: 1px;
    margin: 30px 0 22px;
    background: linear-gradient(90deg, transparent, var(--orange), transparent);
  }
  .section-title, .person-name {
    color: var(--orange);
    font-size: 17px;
    font-weight: 500;
    letter-spacing: 0.5px;
    text-transform: uppercase;
    margin-bottom: 6px;
  }
  .services {
    list-style: none;
    font-size: 15px;
    line-height: 1.35;
    font-weight: 500;
  }
  .contact-line {
    font-size: 15px;
    font-weight: 500;
  }
  .contact-line .label { color: var(--orange); }
</style>
</head>
<body>
  <main class="sheet">
    <section class="card card-front">
      <div class="brand">
        <span class="brand-mark"></span>
        <span class="brand-name">FALCRIDGE HIRES</span>
      </div>
      <div class="divider"></div>
      <h2 class="section-title">Our Services</h2>
      <ul class="services">
        <li>Luxury Restroom Trailers Rental and Sales</li>
        <li>Weddings | Concerts | Charity</li>
        <li>Sporting and Corp | Events</li>
      </ul>
    </section>

    <section class="card card-back">
      <div class="brand">
        <span class="brand-mark"></span>
        <span class="brand-name">FALCRIDGE HIRES</span>
      </div>
      <div class="divider"></div>
      <h2 class="person-name">Dwight Penner</h2>
      <p class="contact-line">CFO | <span class="label">M.</span> 555 318-0476</p>
    </section>
  </main>
</body>
</html>
```